Corporate Travel Technology Company needs new Business Card design

We need a new business card design to reflect our re-branded company. Our company is called tolvEn (pronounced tolvenn) and we provide Business Intelligence and mobile travel management solutions for the corporate travel industry. Our multinational customers use our solutions to manage large travel budgets and frequent travellers, as well as to save money and reduce risk. We'd like to see designs that use the blue and green palette as well as our corporate logo (attached below). The design should communicate innovation, insight, forward thinking, contemporary, trusted.

Target Market(s)

Large multinational corporates and Travel Agencies.

Industry/Entity Type

Business

Contact Information for Business Card

Rosalind Mercer
Chief Executive
tolvEn
Phone number - +61 (0)2 8134 2907
Email address - rosalind.mercer@tolven-example.com
Mobile number - +61 (0)438 516 702
www.tolven-example.com

Font styles to use
Other font styles liked:
• Please use font as close to corporate logo as possible

Colors
0255a3
0393ce
00a990
33b8a4
33a6d7
3176b5

Requirements
Must have
• Please include the words;
• Mobile Travel Management
• Accelerating Travel Business Insights
• Use corporate logo - although icon can be stylised if needed

```html
<!DOCTYPE html>
<html lang="en">
<head>
<meta charset="utf-8">
<title>tolvEn Business Card</title>
<link href="https://fonts.googleapis.com/css2?family=Open+Sans:wght@400;600&display=swap" rel="stylesheet">
<style>
  :root {
    --stage: #e9e7e3;
    --card-white: #f4f5f5;
    --card-black: #050505;
    --brand-blue: #0ea3dc;
    --accent-blue: #0255a3;
    --brand-green: #00a990;
    --soft-green: #33b8a4;
    --name-blue: #1ba0dc;
    --logo-grey: #3f4b50;
    --text-light: #e6e6e6;
    --text-muted: #b9bcbe;
    --divider: #8c8f91;
  }
  * { margin: 0; padding: 0; box-sizing: border-box; }
  html, body { width: 1200px; height: 902px; overflow: hidden; }
  body {
    background: var(--stage);
    font-family: "Open Sans", Arial, sans-serif;
    position: relative;
  }
  .card {
    position: absolute;
    left: 250px;
    width: 700px;
    height: 400px;
    overflow: hidden;
    box-shadow: 0 6px 18px rgba(0,0,0,0.18);
  }
  .card--back { top: 34px; background: var(--brand-blue); }
  .card--front { top: 468px; background: var(--card-white); }

  /* back */
  .back-mark {
    position: absolute;
    left: 0; right: 0; top: 110px;
    display: flex; align-items: center; justify-content: center; gap: 22px;
  }
  .back-mark .mark-dot {
    width: 70px; height: 70px; border-radius: 50%;
    border: 9px solid #fff;
  }
  .back-mark .wordmark {
    color: #fff; font-size: 130px; font-weight: 400; line-height: 1; letter-spacing: -2px;
  }
  .back-tagline {
    position: absolute; left: 0; right: 0; top: 282px;
    text-align: center; color: #fff; font-size: 20px; letter-spacing: 1px;
  }
  .back-stripe {
    position: absolute; left: 0; right: 0; bottom: 0; height: 8px;
    background: linear-gradient(90deg, var(--accent-blue), var(--brand-green));
  }

  /* front */
  .front-brand {
    position: absolute; right: 46px; top: 62px;
    display: flex; align-items: center; gap: 16px;
  }
  .front-brand .mark-dot {
    width: 44px; height: 44px; border-radius: 50%;
    border: 6px solid var(--brand-blue);
  }
  .front-brand .wordmark {
    color: var(--logo-grey); font-size: 92px; font-weight: 400; line-height: 1; letter-spacing: -1px;
  }
  .front-tagline {
    position: absolute; left: 36px; top: 194px;
    color: var(--brand-green); font-size: 16px; font-weight: 600; letter-spacing: 0.5px;
  }
  .rule { position: absolute; left: 0; right: 0; top: 232px; height: 7px; background: var(--accent-blue); }
  .rule-green { position: absolute; left: 0; right: 0; top: 239px; height: 3px; background: var(--soft-green); }
  .panel { position: absolute; left: 0; right: 0; top: 242px; bottom: 0; background: var(--card-black); }

  .identity { position: absolute; left: 36px; top: 300px; }
  .identity .name { color: var(--name-blue); font-size: 28px; font-weight: 400; line-height: 1.2; }
  .identity .role { color: var(--text-muted); font-size: 20px; line-height: 1.4; }

  .divider { position: absolute; left: 352px; top: 268px; width: 1px; height: 110px; background: var(--divider); }

  .contacts { position: absolute; left: 378px; top: 268px; list-style: none; }
  .contacts li {
    display: flex; align-items: center; gap: 12px;
    color: var(--text-light); font-size: 14px; line-height: 27px; white-space: nowrap;
  }
  .contacts svg { width: 12px; height: 12px; flex: none; }
</style>
</head>
<body>

<section class="card card--back" aria-label="Business card back">
  <div class="back-mark">
    <span class="mark-dot"></span>
    <span class="wordmark">tolvEn</span>
  </div>
  <p class="back-tagline">Accelerating Travel Business Insights</p>
  <div class="back-stripe"></div>
</section>

<section class="card card--front" aria-label="Business card front">
  <div class="front-brand">
    <span class="mark-dot"></span>
    <span class="wordmark">tolvEn</span>
  </div>
  <p class="front-tagline">Mobile Travel Management</p>
  <div class="rule"></div>
  <div class="rule-green"></div>
  <div class="panel"></div>

  <div class="identity">
    <p class="name">Rosalind Mercer</p>
    <p class="role">Chief Executive</p>
  </div>

  <div class="divider"></div>

  <ul class="contacts">
    <li>
      <svg viewBox="0 0 12 12" aria-hidden="true"><rect width="12" height="12" rx="2" fill="#0ea3dc"/><path d="M3 4h6v4H3z" fill="none" stroke="#050505" stroke-width="1.2"/></svg>
      +61 (0)2 8134 2907
    </li>
    <li>
      <svg viewBox="0 0 12 12" aria-hidden="true"><path d="M3 1c1 0 2 2 2 3s-1 1-1 2 1 2 2 2 1-1 2-1 3 1 3 2-1 2-2 2C5 11 1 7 1 3c0-1 1-2 2-2z" fill="#0ea3dc"/></svg>
      +61 (0)438 516 702
    </li>
    <li>
      <svg viewBox="0 0 12 12" aria-hidden="true"><rect x="0.5" y="2" width="11" height="8" rx="1" fill="#0ea3dc"/><path d="M1 3l5 4 5-4" fill="none" stroke="#050505" stroke-width="1.1"/></svg>
      rosalind.mercer@tolven-example.com
    </li>
    <li>
      <svg viewBox="0 0 12 12" aria-hidden="true"><circle cx="6" cy="6" r="5" fill="none" stroke="#0ea3dc" stroke-width="1.5"/><path d="M1 6h10M6 1c2 2 2 8 0 10M6 1c-2 2-2 8 0 10" fill="none" stroke="#0ea3dc" stroke-width="1"/></svg>
      www.tolven-example.com
    </li>
  </ul>
</section>

</body>
</html>
```